A5 Patient Information Booklet (Chiropractic Clinic) 4-8 pages

Here’s a polished, professional rewrite of your full brief and content, with clearer structure, corrected language, and a premium tone:

---

**Project Title:** Premium Patient Information Brochure (Chiropractic & Wellness Clinic)

---

### **Overview**

We are a health and wellness clinic seeking a premium, high-end patient information brochure to provide following a patient’s initial consultation and first treatment.

The purpose of this booklet is to:

* Reinforce trust and professionalism
* Help patients understand what to expect next
* Encourage adherence to care recommendations
* Position the clinic as calm, expert-led, and results-driven

---

### **Format**

* 4–8 page booklet (A5 or similar size)
* Print-ready and digital versions required

---

### **Target Audience**

Patients who have just completed their initial consultation and may have begun treatment. They may already be experiencing physical or mental changes, so the brochure should guide, reassure, and educate them on what comes next.

---

### **Tone & Style**

* Premium, calm, and reassuring
* Modern wellness aesthetic (not overly clinical)
* Clean layout with minimal clutter
* Soft, neutral colour palette (whites, creams, muted greens, soft blues)
* Elegant typography (e.g. Montserrat / Lato)
* High-end, trustworthy, and professional feel

---

### **Key Messages**

#### 1. Listen to Your Body

Patients may feel different after treatment. Reassure them that this is normal and part of the healing process.

#### 2. Post-Treatment Advice

* Stay well hydrated
* Rest if needed
* Avoid overexertion if the body requires recovery

#### 3. Healing is a Journey (Core Concept)

A strong visual metaphor of a **“road to recovery”** or **journey** should be central to the design.

This journey should clearly illustrate three phases:

* **Phase 1: Initial Care (Weeks 1–6)**
Focus: Reducing pain/discomfort, calming the body, and initiating response to treatment

* **Phase 2: Corrective Care (Weeks 6–12)**
Focus: Addressing underlying issues, improving function, and creating lasting change

* **Phase 3: Wellness / Maintenance (Ongoing)**
Focus: Maintaining progress, preventing relapse, and supporting long-term wellbeing

**Important:**

* Emphasise that this is not a quick fix
* Progress requires time and consistency
* Each patient follows an individualised care plan
* The journey should feel structured, positive, and achievable

#### 4. Personalised Care

Reinforce that every treatment plan is tailored specifically to the individual.

#### 5. Professional Reassurance

Patients should feel confident they are in expert hands and supported throughout their journey.

---

### **Design Direction**

* Use imagery that reflects calmness, progression, and wellness (e.g. pathways, nature, soft gradients)
* Avoid generic stock imagery
* **Only use original clinic images from website and social media**
* Prioritise white space and clarity
* Aim for a luxury spa/medical hybrid aesthetic

---

## **Content Structure (Page-by-Page)**

### **Front Cover**

* Clean, minimal, premium design
* Clinic branding

---

### **Page 1: Patient Case Summary**

**Title:** *Welcome to Fernwell Spine Studio*

Thank you for choosing Fernwell Spine Studio.

This booklet is designed to guide you through:

* What we found during your initial consultation
* Your personalised recommended treatment plan
* Your road to recovery
* Long-term wellness care
* Why we take the approach we do

---

### **Page 2: Your Care Journey**

**Stage 1: Your Initial Consultation**

Today we completed a comprehensive assessment of your health and function, including:

* Full case history and discussion of your symptoms and goals
* Orthopaedic and neurological testing
* Postural and movement assessment
* Initial treatment (where appropriate)

**What this tells us:**

* How your body is currently functioning
* Where areas of stress or dysfunction may be present
* The most appropriate and effective path forward for your care

---

### **Page 3: Your Suggested Treatment Plan**

Based on today’s findings, your recommended care plan is:

**______ treatments over ______ weeks**

This should be viewed alongside your *Road to Recovery* to help you understand what to expect.

We have also discussed:

* Expected timelines for improvement
* Available payment options

**After Treatment:**
It is common to feel different following treatment. This is a normal response as your body begins to adapt and respond.

We recommend:

* Staying well hydrated
* Allowing time for rest and recovery
* Avoiding overexertion if your body feels it needs it

---

### **Page 4: What to Expect Next**

Healing is not always linear—it is a process that occurs over time.

Your care will typically progress through the following stages:

* **Relief Care**
Focused on reducing discomfort and calming the body

* **Corrective Care**
Focused on addressing underlying issues and improving function
(This phase may include prescribed exercises)

* **Maintenance / Wellness Care**
Focused on sustaining progress, preventing recurrence, and supporting long-term health

---

### **Page 5: Understanding Chiropractic Care**

**What is Chiropractic?**
Chiropractic care focuses on the relationship between the spine, nervous system, and overall body function.

By improving spinal movement and alignment, chiropractic care helps support the nervous system, allowing the body to function and heal more effectively.

**About Fernwell Spine Studio**
At Fernwell Spine Studio, our approach is centred around personalised, patient-focused care. We aim to not only relieve symptoms but to address underlying causes and support long-term wellbeing.

---

### **Back Page**

* Clinic contact details
* Website
* Social media icons/handles

**Closing Message:**
“A healthier, stronger you—supported every step of the way.”

---

### **Deliverables**

* Print-ready PDF
* Editable source files

---

### **Additional Notes**

* The brochure should feel valuable and worth keeping
* Encourage long-term care in a subtle, non-pushy way
* Maintain clarity, readability, and strong visual hierarchy
* Balance professionalism with warmth and approachability

---

If you’d like, I can also turn this into **actual brochure copy (fully written, patient-facing text)** or help you refine it further for a designer.

Existing patients who want to feel better and look after themselves that is given after their initil consultation appointment

Chiropractic, wellness, health

• Montserrat or Lato

0094D4
00A9DD
6FCCEA
C7EBF8
E9F6FB
00AB8E
00BBA5
67D7C9
C6EFE9
E9F9F6
6B429C
8869AF
B7A5CE
E3DAEB
F3F0F8

• my own photos, look premium wellness, be clear and simple to understand for patients journey or what to expect next and over time
• USe my social media/website for ideas
• generic photos and images

```html
<!DOCTYPE html>
<html lang="en">
<head>
<meta charset="utf-8">
<title>Fernwell Spine Studio – Patient Booklet</title>
<link href="https://fonts.googleapis.com/css2?family=Libre+Baskerville:ital,wght@0,400;0,700;1,400;1,700&family=Montserrat:ital,wght@0,400;0,500;0,600;1,400;1,500&display=swap" rel="stylesheet">
<style>
:root{
  --teal:#17a398;
  --teal-deep:#0f8c84;
  --teal-bright:#3cc9c0;
  --teal-soft:#67D7C9;
  --navy:#1f2b45;
  --ink:#3a4150;
  --paper:#f5f6f7;
  --lilac:#d7b9e6;
  --lilac-soft:#E3DAEB;
  --sky:#dfe9f6;
  --orange:#f08a3c;
  --yellow:#f2c230;
  --green:#8cc63f;
  --stage:#d4d6d8;
  --serif:"Libre Baskerville", Georgia, serif;
  --sans:"Montserrat", Arial, sans-serif;
}
*{box-sizing:border-box;margin:0;padding:0}
html,body{width:828px;height:1200px;overflow:hidden;background:var(--stage)}
.canvas{position:relative;width:828px;height:1200px}
.spread{position:absolute;left:24px;width:780px;height:552px;display:flex;box-shadow:0 6px 18px rgba(0,0,0,.18)}
.spread--cover{top:32px}
.spread--inner{top:616px}
.page{position:relative;width:390px;height:552px;overflow:hidden}
.abs{position:absolute}

/* back cover */
.back-cover{background:var(--teal);color:#fff}
.back-cover__photo{left:0;top:0;width:390px;height:330px;background:linear-gradient(160deg,#4fbcb2 0%,#2aa89d 55%,var(--teal) 100%)}
.plan-title{left:0;width:390px;top:206px;text-align:center;font:700 15px var(--serif)}
.plan-card{left:28px;top:240px;width:334px;height:196px;border-radius:18px;background:#f1f3f3;padding:22px 22px 0;color:var(--navy)}
.plan-field{font:400 11px var(--serif);display:flex;align-items:flex-end;gap:6px;margin-bottom:14px}
.plan-field .blank{flex:1;border-bottom:1px solid var(--navy);height:12px}
.plan-field .short{width:60px;flex:none;border-bottom:1px solid var(--navy);height:12px}
.plan-note{font:500 8.5px/1.5 var(--sans);color:var(--teal);margin-top:6px}
.contact{left:0;width:390px;top:458px;text-align:center}
.contact h3{font:700 15px var(--serif);margin-bottom:8px}
.contact p{font:400 9px/1.6 var(--serif)}

/* front cover */
.front-cover{background:linear-gradient(120deg,var(--sky) 0%,#f3f1f7 40%,#ecdff2 70%,var(--lilac) 100%)}
.cover-title{left:0;width:390px;top:70px;text-align:center;font:700 27px/1.3 var(--serif);color:var(--navy)}
.brand{left:0;width:390px;top:190px;display:flex;flex-direction:column;align-items:center;gap:16px}
.brand__dot{width:86px;height:86px;border-radius:50%;border:3px solid var(--teal-soft)}
.brand__name{font:700 20px var(--serif);color:var(--navy)}
.cover-tagline{left:40px;width:310px;top:340px;text-align:center;font:700 13px/1.5 var(--serif);color:var(--navy)}
.cover-motto{left:0;width:390px;top:398px;display:flex;align-items:center;justify-content:center;gap:8px;font:400 13px var(--sans);color:var(--teal)}
.cover-motto .rule{width:60px;height:1px;background:var(--teal);position:relative}
.cover-motto .rule::after{content:"";position:absolute;top:-2px;width:5px;height:5px;border-radius:50%;background:var(--teal)}
.cover-motto .rule--l::after{right:0}
.cover-motto .rule--r::after{left:0}

/* inner left */
.inner-left{background:var(--paper)}
.photo-top{left:0;top:0;width:190px;height:190px;background:linear-gradient(150deg,#e9e6e2,#b7c2cf 60%,#3d4a6a)}
.wave{left:0;top:0;width:390px;height:552px}
.h2{font:700 14px/1.2 var(--serif);color:var(--navy)}
.h2 em{display:block;font-style:italic;color:var(--teal-bright)}
.after{left:200px;top:22px;width:180px}
.body{font:400 8px/1.5 var(--sans);color:var(--ink)}
.body strong{font-weight:600;color:var(--navy)}
.ticks{list-style:none;margin:4px 0}
.ticks li{display:flex;align-items:center;gap:5px;font:400 8px/1.6 var(--sans);color:var(--ink)}
.ticks svg{flex:none}
.post{left:26px;top:262px;width:180px}
.steps{margin-top:12px;display:flex;flex-direction:column;gap:10px}
.step{display:flex;align-items:center;gap:10px;font:500 italic 8.5px/1.35 var(--sans);color:var(--teal)}
.step__label{max-width:120px}
.step__ring{width:36px;height:36px;border-radius:50%;border:2px solid var(--lilac);background:#fff;display:flex;align-items:center;justify-content:center;flex:none}
.post-close{left:26px;top:470px;width:176px;font:italic 400 8px/1.5 var(--sans);color:var(--navy)}
.photo-card{left:214px;top:360px;width:150px;height:170px;border-radius:16px;border:3px solid var(--lilac);background:linear-gradient(160deg,#e4e1e6,#9fb3cc 55%,#3e5475)}

/* inner right */
.inner-right{background:var(--paper)}
.journey-head{left:30px;top:34px}
.band{left:20px;top:82px;width:370px;height:46px;background:var(--teal-bright);padding:7px 14px;color:#fff}
.band h3{font:700 14px var(--serif)}
.band p{font:italic 400 8px var(--sans);margin-top:2px}
.band-lead{left:30px;top:136px;width:340px}
.road{left:10px;top:160px;width:370px;height:110px}
.phase{top:272px;width:100px}
.phase h4{font:500 8.5px var(--sans);margin-bottom:4px}
.phase .when{font:600 8px var(--sans);color:var(--navy);margin-bottom:2px}
.phase--1{left:34px}.phase--1 h4{color:var(--orange)}
.phase--2{left:150px}.phase--2 h4{color:#e0ab1a}
.phase--3{left:268px}.phase--3 h4{color:var(--green)}
.summary{left:30px;top:370px;width:340px}
.expect-head{left:0;width:390px;top:414px;text-align:center}
.expect-head .h2 em{display:inline}
.expect-photo{left:150px;top:440px;width:96px;height:96px;border-radius:50%;border:3px solid var(--lilac);background:linear-gradient(150deg,#f1e3e6,#c9b7b3 50%,#7f8ea8)}
.cue{display:flex;align-items:center;gap:6px;font:400 7.5px/1.35 var(--sans);color:var(--navy)}
.cue__ring{width:22px;height:22px;border-radius:50%;border:1.5px solid var(--lilac);background:#fff;flex:none}
.cue--a{left:34px;top:446px;width:128px;justify-content:flex-end;text-align:right}
.cue--b{left:34px;top:498px;width:128px;justify-content:flex-end;text-align:right}
.cue--c{left:236px;top:446px;width:130px}
.cue--d{left:236px;top:498px;width:130px}
</style>
</head>
<body>
<div class="canvas">

  <section class="spread spread--cover">
    <article class="page back-cover">
      <div class="abs back-cover__photo" role="img" aria-label="Teal-toned photo of a chiropractor treating a patient in the clinic"></div>
      <h2 class="abs plan-title">Your Personalised Plan</h2>
      <div class="abs plan-card">
        <div class="plan-field">Patient Name: <span class="blank"></span></div>
        <div class="plan-field">Your Suggested Care Plan: <span class="blank"></span></div>
        <div class="plan-field"><span class="short"></span> treatments over <span class="short"></span> weeks</div>
        <p class="plan-note">Your care has been designed specifically for your needs, goals, and current condition. We're here to support you throughout your journey—with professional guidance, experience, and ongoing care.</p>
      </div>
      <div class="abs contact">
        <h3>Contact us:</h3>
        <p>12 Alder Row, Harlow Vale, United Kingdom</p>
        <p>info@fernwellspinestudio.co.uk</p>
        <p>www.fernwellspinestudio.co.uk</p>
      </div>
    </article>

    <article class="page front-cover">
      <h1 class="abs cover-title">Your Journey to<br>Better Health</h1>
      <div class="abs brand">
        <span class="brand__dot"></span>
        <span class="brand__name">Fernwell Spine Studio</span>
      </div>
      <p class="abs cover-tagline">A personalised approach to recovery, balance, and long-term wellbeing.</p>
      <p class="abs cover-motto"><span class="rule rule--l"></span>Guided care. Lasting results.<span class="rule rule--r"></span></p>
    </article>
  </section>

  <section class="spread spread--inner">
    <article class="page inner-left">
      <div class="abs photo-top" role="img" aria-label="Photo of a chiropractor assessing a seated patient's back"></div>
      <svg class="abs wave" viewBox="0 0 390 552" aria-hidden="true">
        <path d="M0 205 C120 185 220 235 270 300 C300 330 330 335 350 332" fill="none" stroke="var(--teal-bright)" stroke-width="6"/>
        <path d="M0 198 C120 178 220 228 270 293" fill="none" stroke="var(--teal)" stroke-width="2" opacity=".6"/>
        <circle cx="362" cy="330" r="16" fill="var(--teal-bright)"/>
        <path d="M354 330 L370 324 M354 330 L370 336" stroke="#fff" stroke-width="2" stroke-linecap="round"/>
      </svg>

      <div class="abs after">
        <h2 class="h2">What To Expect <em>After Your Treatment</em></h2>
        <p class="body" style="margin-top:8px">After your first treatment, it's normal to feel different.</p>
        <p class="body" style="margin-top:4px">You may experience subtle changes such as:</p>
        <ul class="ticks">
          <li><svg width="8" height="8" viewBox="0 0 8 8"><circle cx="4" cy="4" r="4" fill="var(--teal)"/><path d="M2 4l1.5 1.5L6 2.8" stroke="#fff" fill="none" stroke-width="1"/></svg>Improved movement or lightness</li>
          <li><svg width="8" height="8" viewBox="0 0 8 8"><circle cx="4" cy="4" r="4" fill="var(--teal)"/><path d="M2 4l1.5 1.5L6 2.8" stroke="#fff" fill="none" stroke-width="1"/></svg>Mild soreness or fatigue</li>
          <li><svg width="8" height="8" viewBox="0 0 8 8"><circle cx="4" cy="4" r="4" fill="var(--teal)"/><path d="M2 4l1.5 1.5L6 2.8" stroke="#fff" fill="none" stroke-width="1"/></svg>A general sense of adjustment</li>
        </ul>
        <p class="body">These are natural responses as your body begins to adapt.</p>
        <p class="body" style="margin-top:4px"><strong>Each person responds in their own way—what matters most is to stay aware and give your body time to process and recover.</strong></p>
      </div>

      <div class="abs post">
        <h2 class="h2">Post-Treatment <em>Care</em></h2>
        <p class="body" style="margin-top:6px">Support your recovery with a few simple steps:</p>
        <div class="steps">
          <div class="step"><span class="step__ring"><svg width="16" height="16" viewBox="0 0 16 16"><path d="M8 2C5 6 4 8 4 10a4 4 0 008 0c0-2-1-4-4-8z" fill="none" stroke="var(--navy)" stroke-width="1.2"/></svg></span><span class="step__label">Stay well hydrated</span></div>
          <div class="step"><span class="step__ring"><svg width="16" height="16" viewBox="0 0 16 16"><path d="M11 3a5 5 0 104 8A6 6 0 0111 3z" fill="none" stroke="var(--navy)" stroke-width="1.2"/></svg></span><span class="step__label">Rest when your body asks for it</span></div>
          <div class="step"><span class="step__ring"><svg width="16" height="16" viewBox="0 0 16 16"><rect x="4" y="3" width="2.5" height="10" fill="none" stroke="var(--navy)" stroke-width="1.2"/><rect x="9.5" y="3" width="2.5" height="10" fill="none" stroke="var(--navy)" stroke-width="1.2"/></svg></span><span class="step__label">Avoid overexertion during recovery</span></div>
        </div>
      </div>
      <p class="abs post-close">Allowing your body the space it needs will help you get the most from your treatment.</p>
      <div class="abs photo-card" role="img" aria-label="Photo of a chiropractor treating a patient's knee on the couch"></div>
    </article>

    <article class="page inner-right">
      <h2 class="abs h2 journey-head">Your Recovery <em>Journey</em></h2>
      <div class="abs band">
        <h3>Healing is a Journey</h3>
        <p>Meaningful, lasting results don't happen overnight.</p>
      </div>
      <p class="abs body band-lead">Your care is designed as a structured journey, supporting your body step by step:</p>
      <svg class="abs road" viewBox="0 0 370 110" aria-hidden="true">
        <defs>
          <linearGradient id="roadGrad" x1="0" x2="1">
            <stop offset="0" stop-color="var(--orange)"/>
            <stop offset=".5" stop-color="var(--yellow)"/>
            <stop offset="1" stop-color="var(--green)"/>
          </linearGradient>
        </defs>
        <path d="M10 30 C50 14 70 20 90 40 C120 70 150 70 190 62 C230 56 260 70 300 84 C330 94 350 90 360 86" fill="none" stroke="url(#roadGrad)" stroke-width="5" stroke-linecap="round"/>
        <circle cx="76" cy="28" r="20" fill="#fff" stroke="var(--orange)" stroke-width="3"/>
        <circle cx="190" cy="62" r="20" fill="#fff" stroke="var(--yellow)" stroke-width="3"/>
        <circle cx="300" cy="84" r="20" fill="#fff" stroke="var(--green)" stroke-width="3"/>
        <path d="M68 28h16M76 20v16" stroke="var(--orange)" stroke-width="1.5"/>
        <path d="M190 52v20M185 57h10M185 63h10M185 69h10" stroke="var(--yellow)" stroke-width="1.5"/>
        <path d="M300 94v-12c-6 0-8-6-8-8 5 0 8 3 8 8 0-5 3-8 8-8 0 2-2 8-8 8" fill="none" stroke="var(--green)" stroke-width="1.5"/>
      </svg>
      <div class="abs phase phase--1">
        <h4>Initial Care</h4>
        <p class="when">Weeks 1–6</p>
        <p class="body">Focus on relieving discomfort, calming the body, and helping you begin to respond to treatment.</p>
      </div>
      <div class="abs phase phase--2">
        <h4>Corrective Care</h4>
        <p class="when">Weeks 6–12</p>
        <p class="body">Address underlying issues, improve function, and build more stable, lasting change.</p>
      </div>
      <div class="abs phase phase--3">
        <h4>Wellness &amp; Maintenance</h4>
        <p class="when">Ongoing</p>
        <p class="body">Maintain progress, prevent setbacks, and support long-term health and balance.</p>
      </div>
      <p class="abs body summary">This process is not a quick fix—it's a guided path toward sustainable results. Your treatment plan is carefully tailored to you, and consistent care plays an important role in achieving the best outcomes.</p>
      <div class="abs expect-head"><h2 class="h2">What to <em>Expect</em></h2></div>
      <div class="abs expect-photo" role="img" aria-label="Round photo of a chiropractor adjusting a patient's shoulder"></div>
      <div class="abs cue cue--a">Healing takes time — results build gradually<span class="cue__ring"></span></div>
      <div class="abs cue cue--b">Every patient responds differently<span class="cue__ring"></span></div>
      <div class="abs cue cue--c"><span class="cue__ring"></span>Consistency is key for lasting improvement</div>
      <div class="abs cue cue--d"><span class="cue__ring"></span>Mild soreness can happen as your body adjusts</div>
    </article>
  </section>

</div>
</body>
</html>
```